Quillmarsh Property Solutions need a business card design

Hello guys. We would need a business card design asap please.
We are a start up property investment business based in London UK specialised in buying, selling, managing and letting properties and helping distressed property owners.
The name of our Business is Quillmarsh, the logo symbolises the four fundamental elements of the world (earth, air, fire and water) and so it stands for strength, stability, longevity.
We would like the business card to communicate professionalism and reliability. Many many thanks indeed for your work.

Details:

1.) Rosalind Updike
Property Investor
Mobile: +44(0)7700123456
Email: rosalind.quillmarsh@mailbox-example.com

2.) Dominic Updike
Property Investor
Mobile: +44(0)7700987654
Email: dominic.quillmarsh@mailbox-example.com

```html
<!DOCTYPE html>
<html lang="en">
<head>
<meta charset="UTF-8">
<title>Quillmarsh Property Solutions – Business Card</title>
<link href="https://fonts.googleapis.com/css2?family=Montserrat:wght@800&family=Open+Sans:wght@400;600;700&display=swap" rel="stylesheet">
<style>
  :root {
    --bg: #e9e6e1;
    --card: #ffffff;
    --ink: #141414;
    --muted: #5a5a5a;
    --name-blue: #1d5fd0;
    --tab-green: #1f9a3a;
    --tab-red: #c8182a;
    --icon-blue: #2a5fb8;
  }
  * { box-sizing: border-box; margin: 0; padding: 0; }
  html, body { width: 1200px; height: 720px; overflow: hidden; }
  body {
    background: var(--bg);
    font-family: "Open Sans", Arial, sans-serif;
    display: flex;
    align-items: center;
    justify-content: center;
    gap: 40px;
  }
  .card {
    position: relative;
    width: 540px;
    height: 308px;
    background: var(--card);
    box-shadow: 0 2px 6px rgba(0,0,0,0.12);
    overflow: hidden;
  }
  .wordmark {
    font-family: "Montserrat", Arial, sans-serif;
    font-weight: 800;
    color: var(--ink);
    text-transform: uppercase;
    line-height: 1.15;
  }
  .wordmark-square {
    display: block;
    background: var(--ink);
  }

  /* Front */
  .card-front .brand { position: absolute; left: 34px; top: 34px; }
  .card-front .wordmark-square { width: 22px; height: 22px; margin-bottom: 14px; }
  .card-front .wordmark-name { font-size: 21px; letter-spacing: 0.5px; }
  .card-front .wordmark-sub { font-size: 9.5px; letter-spacing: 0.6px; margin-left: 26px; }

  .person { position: absolute; right: 30px; top: 74px; text-align: right; }
  .person-name { font-weight: 700; font-size: 16px; color: var(--name-blue); }
  .person-role { font-size: 11px; color: var(--muted); margin-top: 1px; }
  .tab-right {
    position: absolute; right: -8px; top: 66px;
    width: 16px; height: 28px; border-radius: 8px;
    background: var(--tab-green);
  }
  .tab-left {
    position: absolute; left: -8px; top: 212px;
    width: 18px; height: 48px; border-radius: 9px;
    background: var(--tab-red);
  }
  .contacts { position: absolute; left: 32px; top: 212px; list-style: none; }
  .contacts li {
    display: flex; align-items: center; gap: 7px;
    font-size: 12px; color: var(--muted); line-height: 22px;
  }
  .contacts svg { width: 12px; height: 12px; fill: var(--icon-blue); }

  /* Back */
  .card-back .brand {
    position: absolute; left: 0; right: 0; top: 64px;
    display: flex; flex-direction: column; align-items: center;
  }
  .card-back .wordmark-square { width: 40px; height: 40px; margin-bottom: 22px; }
  .card-back .wordmark-name { font-size: 26px; letter-spacing: 0.6px; }
  .card-back .wordmark-sub { font-size: 11px; letter-spacing: 0.8px; }
  .website {
    position: absolute; left: 0; right: 0; bottom: 40px;
    text-align: center; font-size: 15px; letter-spacing: 1.6px; color: #333;
  }
</style>
</head>
<body>

  <section class="card card-front">
    <div class="brand">
      <span class="wordmark-square"></span>
      <div class="wordmark wordmark-name">Quillmarsh</div>
      <div class="wordmark wordmark-sub">Property Solutions</div>
    </div>

    <span class="tab-right"></span>
    <div class="person">
      <div class="person-name">Rosalind Updike</div>
      <div class="person-role">Property Investor</div>
    </div>

    <span class="tab-left"></span>
    <ul class="contacts">
      <li>
        <svg viewBox="0 0 12 12" aria-hidden="true"><path d="M3 0h6a1 1 0 0 1 1 1v10a1 1 0 0 1-1 1H3a1 1 0 0 1-1-1V1a1 1 0 0 1 1-1zm0 1.5v7h6v-7zM6 9.6a.8.8 0 1 0 0 1.6.8.8 0 0 0 0-1.6z"/></svg>
        +44(0)7700123456
      </li>
      <li>
        <svg viewBox="0 0 12 12" aria-hidden="true"><path d="M0 2.5h12v7H0zM1 3.3v.4L6 7l5-3.3v-.4z"/></svg>
        rosalind.quillmarsh@mailbox-example.com
      </li>
    </ul>
  </section>

  <section class="card card-back">
    <div class="brand">
      <span class="wordmark-square"></span>
      <div class="wordmark wordmark-name">Quillmarsh</div>
      <div class="wordmark wordmark-sub">Property Solutions</div>
    </div>
    <div class="website">www.quillmarsh-example.com</div>
  </section>

</body>
</html>
```